Application page web design and internal pages

Create a web site where home
Page looks like an application screen for a mobile phone

Use bold icons and colors with images that have round edges

PorlenPurse Apps is name of page

Search bar at the top

Use colors from Vextaro.org for background

Price of ZORBS in top right corner (https://www.quelvix.example/trade/en-US?symbol=ZORBS_USDT&layout=basic&theme=dark)

Pages within each app should be the same color as the icon

Use the following as app icons on the page:
Key
Icon name: first screen; second screen (text)

⁃ Balances: enter pin; display balances (Your account can hold multiple currency denominations. Your balances are: ZORBS 1234567890)
⁃ Transactions: enter pin; display transactions (Your last 5 payments are ZORBS 10 from Vextaro)
⁃ Send Money: enter phone number, enter amount, send button; display message
⁃ Create Account: choose country code, enter phone number, create button; enter pin; display message ( (phone number) will be notified when their account has been created)
⁃ My Wallet Address: enter pin; display public key (IMPORTANT Send only STELLAR blockchain tokens to this deposit address: GDXQ7PLM2ZNVA9TRK4WSEY8HCBUJ6FOGDLIXP3QM5RTVKNAWZEHOBCYS)
⁃ Private Message: enter phone number, enter message, choose image, send button; enter pin; display message ( (phone number) will be notified when their message has been created)
⁃ Buy Cryptocurrency: drop drown menu of cryptocurrency to purchase (Bitcoin/Ethereum/Stellar/ZORBS), Amount in USD field, amount in chosen cryptocurrency displayed, frequency drop down menu (once/daily/weekly/monthly), buy button; enter card information (name, card number, expiration date, cvv, billing address, zip code), confirm buy button, transactions will appear on your billing statement as VEXTARO; enter pin screen; display message (You will be notified when your coin is received)
⁃ NFTs: upload image, title, description, link media, create NFT button; enter pin screen; display message (You will be notified when your NFT is created)
⁃ Earn: display message (Earn cryptocurrency doing what you do everyday, coming soon)
⁃ Files/Vault: display message (Storage for your photos, documents and more, coming soon)
⁃ Wealth: display message (Build wealth by working with a financial professional to get you to the next level), check box (I would like a financial professional to contact me about building wealth), contact me button; display message (A financial professional will contact you to achieve your financial goals)
⁃ Education: display message (Learn more about everything, coming soon)
⁃ News: display message (News from around the world, coming soon)
⁃ FAQs: use FAQs from this link https://vextaro.example/faq
⁃ Contact Us: enter message, send button; display message (Thank you for reaching out. We will reply to your message in the order it was received. Your patience is appreciated. Blessings.)

Requirements
Must have
• Application home page that looks like the Home Screen of a mobile phone
Nice to have
• Colorful icons

```html
<!DOCTYPE html>
<html lang="en">
<head>
<meta charset="utf-8">
<title>PorlenPurse Apps – Screens</title>
<link href="https://fonts.googleapis.com/css2?family=Montserrat:wght@400;500;600;700&family=Roboto:wght@400;500&display=swap" rel="stylesheet">
<style>
:root{
  --stage:#8b8d90;
  --navy:#1c1a4b;
  --navy-deep:#17153f;
  --page:#e9eef7;
  --white:#ffffff;
  --ink:#2b2b3a;
  --muted:#8a8a95;
  --line:#e1e4ee;
  --accent:#e2467c;
  --tile-art:#6f7fc4;
  --tile-hot:#e0533d;
  --tile-warm:#f29a38;
}
*{box-sizing:border-box;margin:0;padding:0}
html,body{width:1200px;height:533px;overflow:hidden;background:var(--stage)}
body{font-family:"Montserrat",sans-serif;color:var(--ink)}
.defs{position:absolute;width:0;height:0;overflow:hidden}
.board{
  display:grid;
  grid-template-columns:repeat(5,225.5px);
  grid-auto-rows:160.7px;
  column-gap:11.6px;row-gap:13px;
  padding:7.9px 0 0 15.4px;
}
.screen{position:relative;background:var(--page);overflow:hidden}
.sidebar{position:absolute;left:0;top:0;width:49px;height:100%;background:var(--navy);color:var(--white)}
.brand{position:absolute;left:5px;top:4.4px;font-size:4.3px;font-weight:700;white-space:nowrap;letter-spacing:.05px}
.nav{position:absolute;left:4.8px;right:0;top:19.1px;list-style:none}
.nav li{position:relative;height:8.55px;line-height:8.55px;font-size:3.1px;font-weight:600;padding-left:6.4px;white-space:nowrap}
.nav .ico{position:absolute;left:0;top:2.5px;width:3.6px;height:3.6px}
.nav li.active::after{content:"";position:absolute;right:-1.6px;top:2.2px;width:3.4px;height:4.2px;background:var(--page);border-radius:2.1px 0 0 2.1px}
.nav li.active .tab{position:absolute;right:-.9px;top:3.1px;width:2.2px;height:2.4px;z-index:1}
.topbar{position:absolute;left:49px;right:0;top:0;height:17.7px;background:var(--white)}
.search{position:absolute;left:14.8px;top:4.6px;width:60px;height:8.4px;border:.4px solid var(--line);border-radius:4.2px;box-shadow:0 .4px 1.4px rgba(0,0,0,.08);font-family:"Roboto",sans-serif;font-size:2.4px;color:var(--muted);line-height:7.6px;padding-left:4.5px}
.search-btn{position:absolute;right:.8px;top:.8px;width:6px;height:6px;border-radius:50%;background:var(--navy);display:flex;align-items:center;justify-content:center}
.price{position:absolute;left:100.5px;top:4px;width:19.2px;height:9.6px;border:.4px solid var(--line);border-radius:1.2px;font-family:"Roboto",sans-serif;font-size:2.5px;line-height:3.1px;padding:1.5px 0 0 3.4px;color:var(--ink);white-space:nowrap}
.price svg{display:inline-block;width:1.6px;height:1.2px;margin-left:1.2px;vertical-align:.5px}
.auth{position:absolute;right:8.4px;top:6.8px;font-size:2.7px;font-weight:700;color:var(--navy);white-space:nowrap;display:flex;align-items:center;gap:.6px}
.auth svg{width:2.6px;height:2.6px}
.card{position:absolute;left:58.7px;top:26px;width:158.4px;height:122px;background:var(--white);border-radius:18px;display:flex;flex-direction:column;align-items:center;padding-top:19px}
.card.tall{height:125px}
.card-title{height:7px;line-height:7px;font-size:6.2px;font-weight:500;letter-spacing:.15px;color:var(--ink);margin-bottom:9px;white-space:nowrap}
.form{display:flex;flex-direction:column;align-items:center;gap:5px}
.row{display:flex;gap:4.7px}
.field{position:relative;width:43px;height:11px;background:var(--white);border-radius:1px;box-shadow:0 .5px 2px rgba(0,0,0,.13);font-family:"Roboto",sans-serif;font-size:2.3px;color:var(--muted);line-height:11px;padding-left:4.2px;white-space:nowrap}
.field.wide{width:72px}
.field.select::after{content:"";position:absolute;right:2.6px;top:4.8px;width:1px;height:1px;border-right:.3px solid var(--muted);border-bottom:.3px solid var(--muted);transform:rotate(45deg)}
.btn{margin-top:1px;width:25.6px;height:12px;border-radius:1.2px;background:var(--navy);color:var(--white);font-size:2.6px;font-weight:600;line-height:12px;text-align:center;white-space:nowrap}
.copy{width:121px;font-family:"Roboto",sans-serif;font-size:2.6px;line-height:4.8px;color:var(--muted);text-align:center}
.vault{display:flex;gap:10px;margin-top:2px}
.vault-tile{width:33px;height:30px;border-radius:7px;background:linear-gradient(160deg,#262465,var(--navy-deep));display:flex;align-items:center;justify-content:center}
.vault-tile svg{width:20px;height:20px}
.faq{align-items:flex-start;padding:19px 4px 0 15px}
.faq .card-title{align-self:center;margin-left:-11px;margin-bottom:3px}
.faq h3{font-size:4.9px;font-weight:500;line-height:7px;color:var(--ink);margin-top:1px;white-space:nowrap}
.faq ul{list-style:none;margin:.6px 0 1.2px}
.faq li{position:relative;font-family:"Roboto",sans-serif;font-size:1.9px;line-height:2.8px;color:var(--muted);padding-left:6px;margin-bottom:1.4px;max-width:138px}
.faq li::before{content:"";position:absolute;left:0;top:.4px;width:1.8px;height:1.8px;border:.3px solid var(--ink);border-radius:.2px}
</style>
</head>
<body>
<svg class="defs" aria-hidden="true">
  <defs>
    <symbol id="i-bal" viewBox="0 0 12 12"><path d="M1 4.5L6 1.5l5 3z M1.5 10.5h9 M2.8 5.5v4 M5 5.5v4 M7 5.5v4 M9.2 5.5v4" fill="none" stroke="#fff" stroke-width="1.1" stroke-linejoin="round"/></symbol>
    <symbol id="i-tx" viewBox="0 0 12 12"><rect x="1.5" y="1.5" width="9" height="9" rx=".6" fill="none" stroke="#fff" stroke-width="1.1"/><path d="M3.5 4.3h5 M3.5 6h5 M3.5 7.7h3" stroke="#fff" stroke-width="1"/></symbol>
    <symbol id="i-send" viewBox="0 0 12 12"><circle cx="6" cy="6" r="4.6" fill="none" stroke="#fff" stroke-width="1.1"/><path d="M7.4 4.4c-.4-.6-2.8-.8-2.8.5 0 1.4 2.8.8 2.8 2.2 0 1.3-2.4 1.1-2.9.4 M6 2.8v6.4" fill="none" stroke="#fff" stroke-width=".9"/></symbol>
    <symbol id="i-acct" viewBox="0 0 12 12"><circle cx="6" cy="4" r="2.4" fill="none" stroke="#fff" stroke-width="1.1"/><path d="M1.8 11c.4-2.6 2.2-3.8 4.2-3.8s3.8 1.2 4.2 3.8" fill="none" stroke="#fff" stroke-width="1.1"/></symbol>
    <symbol id="i-wallet" viewBox="0 0 12 12"><rect x="1.3" y="2.8" width="9.4" height="7.4" rx="1" fill="none" stroke="#fff" stroke-width="1.1"/><path d="M7.5 5.6h3.2v2.2H7.5z" fill="#fff"/></symbol>
    <symbol id="i-msg" viewBox="0 0 12 12"><rect x="1.2" y="2.6" width="9.6" height="6.8" rx=".8" fill="none" stroke="#fff" stroke-width="1.1"/><path d="M1.5 3l4.5 3.4L10.5 3" fill="none" stroke="#fff" stroke-width="1"/></symbol>
    <symbol id="i-buy" viewBox="0 0 12 12"><path d="M1.5 10.5h9" stroke="#fff" stroke-width="1.1"/><rect x="2.2" y="6" width="1.8" height="4" fill="#fff"/><rect x="5.1" y="3.5" width="1.8" height="6.5" fill="#fff"/><rect x="8" y="1.5" width="1.8" height="8.5" fill="#fff"/></symbol>
    <symbol id="i-nft" viewBox="0 0 12 12"><path d="M6 1l4.4 2.5v5L6 11 1.6 8.5v-5z" fill="none" stroke="#fff" stroke-width="1.1" stroke-linejoin="round"/><circle cx="6" cy="6" r="1.4" fill="#fff"/></symbol>
    <symbol id="i-earn" viewBox="0 0 12 12"><ellipse cx="6.5" cy="3.2" rx="3.5" ry="1.5" fill="none" stroke="#fff" stroke-width="1"/><path d="M3 3.2v2.6c0 .8 1.6 1.5 3.5 1.5S10 6.6 10 5.8V3.2 M1.5 9.5h3l2 1.2 3.5-1.2" fill="none" stroke="#fff" stroke-width="1"/></symbol>
    <symbol id="i-files" viewBox="0 0 12 12"><path d="M1.2 3h3.4l1 1.2h5.2v5.8H1.2z" fill="none" stroke="#fff" stroke-width="1.1" stroke-linejoin="round"/></symbol>
    <symbol id="i-wealth" viewBox="0 0 12 12"><path d="M6 11V5.5 M6 6.8C6 4.6 4.4 3.4 2.2 3.4c0 2.2 1.6 3.4 3.8 3.4z M6 5.5c0-2.2 1.6-3.6 3.8-3.6 0 2.2-1.6 3.6-3.8 3.6z M3.5 11h5" fill="none" stroke="#fff" stroke-width="1" stroke-linejoin="round"/></symbol>
    <symbol id="i-edu" viewBox="0 0 12 12"><path d="M6 3.2C4.8 2.3 3 2 1.3 2.2v7.4C3 9.4 4.8 9.7 6 10.6c1.2-.9 3-1.2 4.7-1V2.2C9 2 7.2 2.3 6 3.2z M6 3.2v7.4" fill="none" stroke="#fff" stroke-width="1" stroke-linejoin="round"/></symbol>
    <symbol id="i-news" viewBox="0 0 12 12"><rect x="1.5" y="2" width="9" height="8" rx=".5" fill="none" stroke="#fff" stroke-width="1.1"/><rect x="3" y="3.6" width="2.6" height="2.4" fill="#fff"/><path d="M6.6 4h2.5 M6.6 5.6h2.5 M3 7.6h6" stroke="#fff" stroke-width=".9"/></symbol>
    <symbol id="i-faq" viewBox="0 0 12 12"><path d="M1.5 2h9v6.2H5.2L2.8 10.3V8.2H1.5z" fill="none" stroke="#fff" stroke-width="1.1" stroke-linejoin="round"/><path d="M4.9 4.2c0-.8.5-1.2 1.1-1.2s1.1.4 1.1 1c0 .8-1.1.8-1.1 1.6" fill="none" stroke="#fff" stroke-width=".9"/><circle cx="6" cy="6.8" r=".45" fill="#fff"/></symbol>
    <symbol id="i-contact" viewBox="0 0 12 12"><path d="M3 1.5l1.7 2.4-1 1.2c.6 1.4 1.6 2.4 3.1 3.1l1.2-1 2.4 1.7-.9 1.8C5.6 10.6 1.4 6.4 1.3 2.4z" fill="none" stroke="#fff" stroke-width="1" stroke-linejoin="round"/></symbol>
    <symbol id="i-tab" viewBox="0 0 4 4"><path d="M3 .5L1.2 2 3 3.5" fill="none" stroke="#e2467c" stroke-width=".8"/></symbol>
    <symbol id="i-search" viewBox="0 0 10 10"><circle cx="4.2" cy="4.2" r="2.8" fill="none" stroke="#fff" stroke-width="1.4"/><line x1="6.3" y1="6.3" x2="8.6" y2="8.6" stroke="#fff" stroke-width="1.4"/></symbol>
    <symbol id="i-user" viewBox="0 0 10 10"><circle cx="5" cy="3" r="2.4" fill="#1c1a4b"/><path d="M1 10a4 4 0 0 1 8 0z" fill="#1c1a4b"/></symbol>
    <symbol id="i-signin" viewBox="0 0 10 10"><path d="M1 4h5V2l3 3-3 3V6H1z" fill="#1c1a4b"/></symbol>
    <symbol id="i-up" viewBox="0 0 4 3"><path d="M.4 2.6L2 .8l1.6 1.8" fill="none" stroke="#2b2b3a" stroke-width=".7"/></symbol>
  </defs>
</svg>

<main class="board">

<!-- Balances -->
<section class="screen">
  <aside class="sidebar"><div class="brand">PorlenPurse Apps</div>
    <ul class="nav">
      <li class="active"><svg class="ico"><use href="#i-bal"/></svg>Balances<svg class="tab"><use href="#i-tab"/></svg></li>
      <li><svg class="ico"><use href="#i-tx"/></svg>Transactions</li>
      <li><svg class="ico"><use href="#i-send"/></svg>Send Money</li>
      <li><svg class="ico"><use href="#i-acct"/></svg>Create Account</li>
      <li><svg class="ico"><use href="#i-wallet"/></svg>My Wallet Address</li>
      <li><svg class="ico"><use href="#i-msg"/></svg>Private Message</li>
      <li><svg class="ico"><use href="#i-buy"/></svg>Buy Cryptocurrency</li>
      <li><svg class="ico"><use href="#i-nft"/></svg>NFTS</li>
      <li><svg class="ico"><use href="#i-earn"/></svg>Earn</li>
      <li><svg class="ico"><use href="#i-files"/></svg>Files/Vault</li>
      <li><svg class="ico"><use href="#i-wealth"/></svg>Wealth</li>
      <li><svg class="ico"><use href="#i-edu"/></svg>Education</li>
      <li><svg class="ico"><use href="#i-news"/></svg>News</li>
      <li><svg class="ico"><use href="#i-faq"/></svg>FAQS</li>
      <li><svg class="ico"><use href="#i-contact"/></svg>Contact Us</li>
    </ul></aside>
  <header class="topbar"><div class="search">Search<span class="search-btn"><svg width="3" height="3"><use href="#i-search"/></svg></span></div>
    <div class="price">ZORBS<svg><use href="#i-up"/></svg><br>$ 1.75</div>
    <div class="auth"><svg><use href="#i-user"/></svg>LOGIN / <svg><use href="#i-signin"/></svg>SIGN UP</div></header>
  <div class="card"><h2 class="card-title">BALANCES</h2>
    <div class="form"><div class="field wide">Enter pin</div></div></div>
</section>

<!-- Transactions -->
<section class="screen">
  <aside class="sidebar"><div class="brand">PorlenPurse Apps</div>
    <ul class="nav">
      <li><svg class="ico"><use href="#i-bal"/></svg>Balances</li>
      <li class="active"><svg class="ico"><use href="#i-tx"/></svg>Transactions<svg class="tab"><use href="#i-tab"/></svg></li>
      <li><svg class="ico"><use href="#i-send"/></svg>Send Money</li>
      <li><svg class="ico"><use href="#i-acct"/></svg>Create Account</li>
      <li><svg class="ico"><use href="#i-wallet"/></svg>My Wallet Address</li>
      <li><svg class="ico"><use href="#i-msg"/></svg>Private Message</li>
      <li><svg class="ico"><use href="#i-buy"/></svg>Buy Cryptocurrency</li>
      <li><svg class="ico"><use href="#i-nft"/></svg>NFTS</li>
      <li><svg class="ico"><use href="#i-earn"/></svg>Earn</li>
      <li><svg class="ico"><use href="#i-files"/></svg>Files/Vault</li>
      <li><svg class="ico"><use href="#i-wealth"/></svg>Wealth</li>
      <li><svg class="ico"><use href="#i-edu"/></svg>Education</li>
      <li><svg class="ico"><use href="#i-news"/></svg>News</li>
      <li><svg class="ico"><use href="#i-faq"/></svg>FAQS</li>
      <li><svg class="ico"><use href="#i-contact"/></svg>Contact Us</li>
    </ul></aside>
  <header class="topbar"><div class="search">Search<span class="search-btn"><svg width="3" height="3"><use href="#i-search"/></svg></span></div>
    <div class="price">ZORBS<svg><use href="#i-up"/></svg><br>$ 1.75</div>
    <div class="auth"><svg><use href="#i-user"/></svg>LOGIN / <svg><use href="#i-signin"/></svg>SIGN UP</div></header>
  <div class="card"><h2 class="card-title">TRANSACTIONS</h2>
    <div class="form"><div class="field wide">Enter pin</div></div></div>
</section>

<!-- Send Money -->
<section class="screen">
  <aside class="sidebar"><div class="brand">PorlenPurse Apps</div>
    <ul class="nav">
      <li><svg class="ico"><use href="#i-bal"/></svg>Balances</li>
      <li><svg class="ico"><use href="#i-tx"/></svg>Transactions</li>
      <li class="active"><svg class="ico"><use href="#i-send"/></svg>Send Money<svg class="tab"><use href="#i-tab"/></svg></li>
      <li><svg class="ico"><use href="#i-acct"/></svg>Create Account</li>
      <li><svg class="ico"><use href="#i-wallet"/></svg>My Wallet Address</li>
      <li><svg class="ico"><use href="#i-msg"/></svg>Private Message</li>
      <li><svg class="ico"><use href="#i-buy"/></svg>Buy Cryptocurrency</li>
      <li><svg class="ico"><use href="#i-nft"/></svg>NFTS</li>
      <li><svg class="ico"><use href="#i-earn"/></svg>Earn</li>
      <li><svg class="ico"><use href="#i-files"/></svg>Files/Vault</li>
      <li><svg class="ico"><use href="#i-wealth"/></svg>Wealth</li>
      <li><svg class="ico"><use href="#i-edu"/></svg>Education</li>
      <li><svg class="ico"><use href="#i-news"/></svg>News</li>
      <li><svg class="ico"><use href="#i-faq"/></svg>FAQS</li>
      <li><svg class="ico"><use href="#i-contact"/></svg>Contact Us</li>
    </ul></aside>
  <header class="topbar"><div class="search">Search<span class="search-btn"><svg width="3" height="3"><use href="#i-search"/></svg></span></div>
    <div class="price">ZORBS<svg><use href="#i-up"/></svg><br>$ 1.75</div>
    <div class="auth"><svg><use href="#i-user"/></svg>LOGIN / <svg><use href="#i-signin"/></svg>SIGN UP</div></header>
  <div class="card"><h2 class="card-title">SEND MONEY</h2>
    <div class="form"><div class="row"><div class="field">Enter phone number</div><div class="field">Enter amount</div></div>
      <div class="btn">SEND</div></div></div>
</section>

<!-- Create Account -->
<section class="screen">
  <aside class="sidebar"><div class="brand">PorlenPurse Apps</div>
    <ul class="nav">
      <li><svg class="ico"><use href="#i-bal"/></svg>Balances</li>
      <li><svg class="ico"><use href="#i-tx"/></svg>Transactions</li>
      <li><svg class="ico"><use href="#i-send"/></svg>Send Money</li>
      <li class="active"><svg class="ico"><use href="#i-acct"/></svg>Create Account<svg class="tab"><use href="#i-tab"/></svg></li>
      <li><svg class="ico"><use href="#i-wallet"/></svg>My Wallet Address</li>
      <li><svg class="ico"><use href="#i-msg"/></svg>Private Message</li>
      <li><svg class="ico"><use href="#i-buy"/></svg>Buy Cryptocurrency</li>
      <li><svg class="ico"><use href="#i-nft"/></svg>NFTS</li>
      <li><svg class="ico"><use href="#i-earn"/></svg>Earn</li>
      <li><svg class="ico"><use href="#i-files"/></svg>Files/Vault</li>
      <li><svg class="ico"><use href="#i-wealth"/></svg>Wealth</li>
      <li><svg class="ico"><use href="#i-edu"/></svg>Education</li>
      <li><svg class="ico"><use href="#i-news"/></svg>News</li>
      <li><svg class="ico"><use href="#i-faq"/></svg>FAQS</li>
      <li><svg class="ico"><use href="#i-contact"/></svg>Contact Us</li>
    </ul></aside>
  <header class="topbar"><div class="search">Search<span class="search-btn"><svg width="3" height="3"><use href="#i-search"/></svg></span></div>
    <div class="price">ZORBS<svg><use href="#i-up"/></svg><br>$ 1.75</div>
    <div class="auth"><svg><use href="#i-user"/></svg>LOGIN / <svg><use href="#i-signin"/></svg>SIGN UP</div></header>
  <div class="card"><h2 class="card-title">CREATE ACCOUNT</h2>
    <div class="form"><div class="row"><div class="field">Choose country code</div><div class="field">Enter phone number</div><div class="field">Enter pin</div></div>
      <div class="btn">CREATE</div></div></div>
</section>

<!-- My Wallet Address -->
<section class="screen">
  <aside class="sidebar"><div class="brand">PorlenPurse Apps</div>
    <ul class="nav">
      <li><svg class="ico"><use href="#i-bal"/></svg>Balances</li>
      <li><svg class="ico"><use href="#i-tx"/></svg>Transactions</li>
      <li><svg class="ico"><use href="#i-send"/></svg>Send Money</li>
      <li><svg class="ico"><use href="#i-acct"/></svg>Create Account</li>
      <li class="active"><svg class="ico"><use href="#i-wallet"/></svg>My Wallet Address<svg class="tab"><use href="#i-tab"/></svg></li>
      <li><svg class="ico"><use href="#i-msg"/></svg>Private Message</li>
      <li><svg class="ico"><use href="#i-buy"/></svg>Buy Cryptocurrency</li>
      <li><svg class="ico"><use href="#i-nft"/></svg>NFTS</li>
      <li><svg class="ico"><use href="#i-earn"/></svg>Earn</li>
      <li><svg class="ico"><use href="#i-files"/></svg>Files/Vault</li>
      <li><svg class="ico"><use href="#i-wealth"/></svg>Wealth</li>
      <li><svg class="ico"><use href="#i-edu"/></svg>Education</li>
      <li><svg class="ico"><use href="#i-news"/></svg>News</li>
      <li><svg class="ico"><use href="#i-faq"/></svg>FAQS</li>
      <li><svg class="ico"><use href="#i-contact"/></svg>Contact Us</li>
    </ul></aside>
  <header class="topbar"><div class="search">Search<span class="search-btn"><svg width="3" height="3"><use href="#i-search"/></svg></span></div>
    <div class="price">ZORBS<svg><use href="#i-up"/></svg><br>$ 1.75</div>
    <div class="auth"><svg><use href="#i-user"/></svg>LOGIN / <svg><use href="#i-signin"/></svg>SIGN UP</div></header>
  <div class="card"><h2 class="card-title">MY WALLET ADDRESS</h2>
    <div class="form"><div class="field">Enter pin</div></div></div>
</section>

<!-- Private Message -->
<section class="screen">
  <aside class="sidebar"><div class="brand">PorlenPurse Apps</div>
    <ul class="nav">
      <li><svg class="ico"><use href="#i-bal"/></svg>Balances</li>
      <li><svg class="ico"><use href="#i-tx"/></svg>Transactions</li>
      <li><svg class="ico"><use href="#i-send"/></svg>Send Money</li>
      <li><svg class="ico"><use href="#i-acct"/></svg>Create Account</li>
      <li><svg class="ico"><use href="#i-wallet"/></svg>My Wallet Address</li>
      <li class="active"><svg class="ico"><use href="#i-msg"/></svg>Private Message<svg class="tab"><use href="#i-tab"/></svg></li>
      <li><svg class="ico"><use href="#i-buy"/></svg>Buy Cryptocurrency</li>
      <li><svg class="ico"><use href="#i-nft"/></svg>NFTS</li>
      <li><svg class="ico"><use href="#i-earn"/></svg>Earn</li>
      <li><svg class="ico"><use href="#i-files"/></svg>Files/Vault</li>
      <li><svg class="ico"><use href="#i-wealth"/></svg>Wealth</li>
      <li><svg class="ico"><use href="#i-edu"/></svg>Education</li>
      <li><svg class="ico"><use href="#i-news"/></svg>News</li>
      <li><svg class="ico"><use href="#i-faq"/></svg>FAQS</li>
      <li><svg class="ico"><use href="#i-contact"/></svg>Contact Us</li>
    </ul></aside>
  <header class="topbar"><div class="search">Search<span class="search-btn"><svg width="3" height="3"><use href="#i-search"/></svg></span></div>
    <div class="price">ZORBS<svg><use href="#i-up"/></svg><br>$ 1.75</div>
    <div class="auth"><svg><use href="#i-user"/></svg>LOGIN / <svg><use href="#i-signin"/></svg>SIGN UP</div></header>
  <div class="card"><h2 class="card-title">PRIVATE MESSAGE</h2>
    <div class="form"><div class="row"><div class="field">Enter phone number</div><div class="field">Enter message</div></div>
      <div class="row"><div class="field">Choose image</div><div class="field">Enter pin</div></div>
      <div class="btn">SEND</div></div></div>
</section>

<!-- Buy Cryptocurrency -->
<section class="screen">
  <aside class="sidebar"><div class="brand">PorlenPurse Apps</div>
    <ul class="nav">
      <li><svg class="ico"><use href="#i-bal"/></svg>Balances</li>
      <li><svg class="ico"><use href="#i-tx"/></svg>Transactions</li>
      <li><svg class="ico"><use href="#i-send"/></svg>Send Money</li>
      <li><svg class="ico"><use href="#i-acct"/></svg>Create Account</li>
      <li><svg class="ico"><use href="#i-wallet"/></svg>My Wallet Address</li>
      <li><svg class="ico"><use href="#i-msg"/></svg>Private Message</li>
      <li class="active"><svg class="ico"><use href="#i-buy"/></svg>Buy Cryptocurrency<svg class="tab"><use href="#i-tab"/></svg></li>
      <li><svg class="ico"><use href="#i-nft"/></svg>NFTS</li>
      <li><svg class="ico"><use href="#i-earn"/></svg>Earn</li>
      <li><svg class="ico"><use href="#i-files"/></svg>Files/Vault</li>
      <li><svg class="ico"><use href="#i-wealth"/></svg>Wealth</li>
      <li><svg class="ico"><use href="#i-edu"/></svg>Education</li>
      <li><svg class="ico"><use href="#i-news"/></svg>News</li>
      <li><svg class="ico"><use href="#i-faq"/></svg>FAQS</li>
      <li><svg class="ico"><use href="#i-contact"/></svg>Contact Us</li>
    </ul></aside>
  <header class="topbar"><div class="search">Search<span class="search-btn"><svg width="3" height="3"><use href="#i-search"/></svg></span></div>
    <div class="price">ZORBS<svg><use href="#i-up"/></svg><br>$ 1.75</div>
    <div class="auth"><svg><use href="#i-user"/></svg>LOGIN / <svg><use href="#i-signin"/></svg>SIGN UP</div></header>
  <div class="card"><h2 class="card-title">BUY CRYPTOCURRENCY</h2>
    <div class="form"><div class="row"><div class="field select">Cryptocurrency to purchase</div><div class="field">Amount in USD field</div><div class="field select">Frequency</div></div>
      <div class="btn">BUY</div></div></div>
</section>

<!-- NFTs -->
<section class="screen">
  <aside class="sidebar"><div class="brand">PorlenPurse Apps</div>
    <ul class="nav">
      <li><svg class="ico"><use href="#i-bal"/></svg>Balances</li>
      <li><svg class="ico"><use href="#i-tx"/></svg>Transactions</li>
      <li><svg class="ico"><use href="#i-send"/></svg>Send Money</li>
      <li><svg class="ico"><use href="#i-acct"/></svg>Create Account</li>
      <li><svg class="ico"><use href="#i-wallet"/></svg>My Wallet Address</li>
      <li><svg class="ico"><use href="#i-msg"/></svg>Private Message</li>
      <li><svg class="ico"><use href="#i-buy"/></svg>Buy Cryptocurrency</li>
      <li class="active"><svg class="ico"><use href="#i-nft"/></svg>NFTS<svg class="tab"><use href="#i-tab"/></svg></li>
      <li><svg class="ico"><use href="#i-earn"/></svg>Earn</li>
      <li><svg class="ico"><use href="#i-files"/></svg>Files/Vault</li>
      <li><svg class="ico"><use href="#i-wealth"/></svg>Wealth</li>
      <li><svg class="ico"><use href="#i-edu"/></svg>Education</li>
      <li><svg class="ico"><use href="#i-news"/></svg>News</li>
      <li><svg class="ico"><use href="#i-faq"/></svg>FAQS</li>
      <li><svg class="ico"><use href="#i-contact"/></svg>Contact Us</li>
    </ul></aside>
  <header class="topbar"><div class="search">Search<span class="search-btn"><svg width="3" height="3"><use href="#i-search"/></svg></span></div>
    <div class="price">ZORBS<svg><use href="#i-up"/></svg><br>$ 1.75</div>
    <div class="auth"><svg><use href="#i-user"/></svg>LOGIN / <svg><use href="#i-signin"/></svg>SIGN UP</div></header>
  <div class="card"><h2 class="card-title">NFTS</h2>
    <div class="form"><div class="row"><div class="field">Upload image</div><div class="field">Title</div></div>
      <div class="row"><div class="field">Description</div><div class="field">Link media</div></div>
      <div class="btn">CREATE NFT</div></div></div>
</section>

<!-- Earn -->
<section class="screen">
  <aside class="sidebar"><div class="brand">PorlenPurse Apps</div>
    <ul class="nav">
      <li><svg class="ico"><use href="#i-bal"/></svg>Balances</li>
      <li><svg class="ico"><use href="#i-tx"/></svg>Transactions</li>
      <li><svg class="ico"><use href="#i-send"/></svg>Send Money</li>
      <li><svg class="ico"><use href="#i-acct"/></svg>Create Account</li>
      <li><svg class="ico"><use href="#i-wallet"/></svg>My Wallet Address</li>
      <li><svg class="ico"><use href="#i-msg"/></svg>Private Message</li>
      <li><svg class="ico"><use href="#i-buy"/></svg>Buy Cryptocurrency</li>
      <li><svg class="ico"><use href="#i-nft"/></svg>NFTS</li>
      <li class="active"><svg class="ico"><use href="#i-earn"/></svg>Earn<svg class="tab"><use href="#i-tab"/></svg></li>
      <li><svg class="ico"><use href="#i-files"/></svg>Files/Vault</li>
      <li><svg class="ico"><use href="#i-wealth"/></svg>Wealth</li>
      <li><svg class="ico"><use href="#i-edu"/></svg>Education</li>
      <li><svg class="ico"><use href="#i-news"/></svg>News</li>
      <li><svg class="ico"><use href="#i-faq"/></svg>FAQS</li>
      <li><svg class="ico"><use href="#i-contact"/></svg>Contact Us</li>
    </ul></aside>
  <header class="topbar"><div class="search">Search<span class="search-btn"><svg width="3" height="3"><use href="#i-search"/></svg></span></div>
    <div class="price">ZORBS<svg><use href="#i-up"/></svg><br>$ 1.75</div>
    <div class="auth"><svg><use href="#i-user"/></svg>LOGIN / <svg><use href="#i-signin"/></svg>SIGN UP</div></header>
  <div class="card"><h2 class="card-title">EARN</h2>
    <p class="copy">Lorem ipsum dolor sit amet, consectetur adipiscing elit, sed do eiusmod tempor incididunt ut labore et dolore magna aliqua. Ut enim ad minim veniam, quis nostrud exercitation ullamco laboris nisi ut aliquip ex ea commodo consequat. Duis aute irure dolor in reprehenderit in voluptate velit esse cillum dolore eu fugiat nulla pariatur. Excepteur sint occaecat cupidatat non proident, sunt in culpa qui officia deserunt mollit anim id est laborum.</p></div>
</section>

<!-- Files/Vault -->
<section class="screen">
  <aside class="sidebar"><div class="brand">PorlenPurse Apps</div>
    <ul class="nav">
      <li><svg class="ico"><use href="#i-bal"/></svg>Balances</li>
      <li><svg class="ico"><use href="#i-tx"/></svg>Transactions</li>
      <li><svg class="ico"><use href="#i-send"/></svg>Send Money</li>
      <li><svg class="ico"><use href="#i-acct"/></svg>Create Account</li>
      <li><svg class="ico"><use href="#i-wallet"/></svg>My Wallet Address</li>
      <li><svg class="ico"><use href="#i-msg"/></svg>Private Message</li>
      <li><svg class="ico"><use href="#i-buy"/></svg>Buy Cryptocurrency</li>
      <li><svg class="ico"><use href="#i-nft"/></svg>NFTS</li>
      <li><svg class="ico"><use href="#i-earn"/></svg>Earn</li>
      <li class="active"><svg class="ico"><use href="#i-files"/></svg>Files/Vault<svg class="tab"><use href="#i-tab"/></svg></li>
      <li><svg class="ico"><use href="#i-wealth"/></svg>Wealth</li>
      <li><svg class="ico"><use href="#i-edu"/></svg>Education</li>
      <li><svg class="ico"><use href="#i-news"/></svg>News</li>
      <li><svg class="ico"><use href="#i-faq"/></svg>FAQS</li>
      <li><svg class="ico"><use href="#i-contact"/></svg>Contact Us</li>
    </ul></aside>
  <header class="topbar"><div class="search">Search<span class="search-btn"><svg width="3" height="3"><use href="#i-search"/></svg></span></div>
    <div class="price">ZORBS<svg><use href="#i-up"/></svg><br>$ 1.75</div>
    <div class="auth"><svg><use href="#i-user"/></svg>LOGIN / <svg><use href="#i-signin"/></svg>SIGN UP</div></header>
  <div class="card"><h2 class="card-title">FILES/VAULT</h2>
    <div class="vault">
      <div class="vault-tile" role="img" aria-label="Inbox app icon">
        <svg viewBox="0 0 20 20"><path d="M3 9l2.5-5h9L17 9v7H3z" fill="var(--tile-art)"/><path d="M3 9h4.5l1 2h3l1-2H17" fill="none" stroke="#1c1a4b" stroke-width="1"/><circle cx="14.5" cy="5" r="2.2" fill="var(--tile-hot)"/></svg>
      </div>
      <div class="vault-tile" role="img" aria-label="Chat app icon">
        <svg viewBox="0 0 20 20"><path d="M2 5h10v6H6l-3 2.5V11H2z" fill="var(--tile-art)"/><path d="M8 8.5h10v6h-1V17l-3-2.5H8z" fill="var(--tile-warm)"/><circle cx="11" cy="11.5" r=".8" fill="#1c1a4b"/><circle cx="13" cy="11.5" r=".8" fill="#1c1a4b"/><circle cx="15" cy="11.5" r=".8" fill="#1c1a4b"/></svg>
      </div>
      <div class="vault-tile" role="img" aria-label="Phone call app icon">
        <svg viewBox="0 0 20 20"><path d="M5 3.5l2.6 3.6-1.5 1.8c.9 2.1 2.4 3.6 4.7 4.7l1.8-1.5 3.6 2.6-1.4 2.7C8.6 17.3 2.7 11.4 2.5 4.9z" fill="var(--tile-art)"/><circle cx="14" cy="6" r="3.4" fill="var(--tile-hot)"/><path d="M12.5 6h3 M14 4.5v3" stroke="var(--tile-warm)" stroke-width=".9"/></svg>
      </div>
    </div></div>
</section>

<!-- Wealth -->
<section class="screen">
  <aside class="sidebar"><div class="brand">PorlenPurse Apps</div>
    <ul class="nav">
      <li><svg class="ico"><use href="#i-bal"/></svg>Balances</li>
      <li><svg class="ico"><use href="#i-tx"/></svg>Transactions</li>
      <li><svg class="ico"><use href="#i-send"/></svg>Send Money</li>
      <li><svg class="ico"><use href="#i-acct"/></svg>Create Account</li>
      <li><svg class="ico"><use href="#i-wallet"/></svg>My Wallet Address</li>
      <li><svg class="ico"><use href="#i-msg"/></svg>Private Message</li>
      <li><svg class="ico"><use href="#i-buy"/></svg>Buy Cryptocurrency</li>
      <li><svg class="ico"><use href="#i-nft"/></svg>NFTS</li>
      <li><svg class="ico"><use href="#i-earn"/></svg>Earn</li>
      <li><svg class="ico"><use href="#i-files"/></svg>Files/Vault</li>
      <li class="active"><svg class="ico"><use href="#i-wealth"/></svg>Wealth<svg class="tab"><use href="#i-tab"/></svg></li>
      <li><svg class="ico"><use href="#i-edu"/></svg>Education</li>
      <li><svg class="ico"><use href="#i-news"/></svg>News</li>
      <li><svg class="ico"><use href="#i-faq"/></svg>FAQS</li>
      <li><svg class="ico"><use href="#i-contact"/></svg>Contact Us</li>
    </ul></aside>
  <header class="topbar"><div class="search">Search<span class="search-btn"><svg width="3" height="3"><use href="#i-search"/></svg></span></div>
    <div class="price">ZORBS<svg><use href="#i-up"/></svg><br>$ 1.75</div>
    <div class="auth"><svg><use href="#i-user"/></svg>LOGIN / <svg><use href="#i-signin"/></svg>SIGN UP</div></header>
  <div class="card"><h2 class="card-title">WEALTH</h2>
    <p class="copy">Lorem ipsum dolor sit amet, consectetur adipiscing elit, sed do eiusmod tempor incididunt ut labore et dolore magna aliqua. Ut enim ad minim veniam, quis nostrud exercitation ullamco laboris nisi ut aliquip ex ea commodo consequat. Duis aute irure dolor in reprehenderit in voluptate velit esse cillum dolore eu fugiat nulla pariatur. Excepteur sint occaecat cupidatat non proident, sunt in culpa qui officia deserunt mollit anim id est laborum.</p></div>
</section>

<!-- Education -->
<section class="screen">
  <aside class="sidebar"><div class="brand">PorlenPurse Apps</div>
    <ul class="nav">
      <li><svg class="ico"><use href="#i-bal"/></svg>Balances</li>
      <li><svg class="ico"><use href="#i-tx"/></svg>Transactions</li>
      <li><svg class="ico"><use href="#i-send"/></svg>Send Money</li>
      <li><svg class="ico"><use href="#i-acct"/></svg>Create Account</li>
      <li><svg class="ico"><use href="#i-wallet"/></svg>My Wallet Address</li>
      <li><svg class="ico"><use href="#i-msg"/></svg>Private Message</li>
      <li><svg class="ico"><use href="#i-buy"/></svg>Buy Cryptocurrency</li>
      <li><svg class="ico"><use href="#i-nft"/></svg>NFTS</li>
      <li><svg class="ico"><use href="#i-earn"/></svg>Earn</li>
      <li><svg class="ico"><use href="#i-files"/></svg>Files/Vault</li>
      <li><svg class="ico"><use href="#i-wealth"/></svg>Wealth</li>
      <li class="active"><svg class="ico"><use href="#i-edu"/></svg>Education<svg class="tab"><use href="#i-tab"/></svg></li>
      <li><svg class="ico"><use href="#i-news"/></svg>News</li>
      <li><svg class="ico"><use href="#i-faq"/></svg>FAQS</li>
      <li><svg class="ico"><use href="#i-contact"/></svg>Contact Us</li>
    </ul></aside>
  <header class="topbar"><div class="search">Search<span class="search-btn"><svg width="3" height="3"><use href="#i-search"/></svg></span></div>
    <div class="price">ZORBS<svg><use href="#i-up"/></svg><br>$ 1.75</div>
    <div class="auth"><svg><use href="#i-user"/></svg>LOGIN / <svg><use href="#i-signin"/></svg>SIGN UP</div></header>
  <div class="card"><h2 class="card-title">EDUCATION</h2>
    <p class="copy">Lorem ipsum dolor sit amet, consectetur adipiscing elit, sed do eiusmod tempor incididunt ut labore et dolore magna aliqua. Ut enim ad minim veniam, quis nostrud exercitation ullamco laboris nisi ut aliquip ex ea commodo consequat. Duis aute irure dolor in reprehenderit in voluptate velit esse cillum dolore eu fugiat nulla pariatur. Excepteur sint occaecat cupidatat non proident, sunt in culpa qui officia deserunt mollit anim id est laborum.</p></div>
</section>

<!-- News -->
<section class="screen">
  <aside class="sidebar"><div class="brand">PorlenPurse Apps</div>
    <ul class="nav">
      <li><svg class="ico"><use href="#i-bal"/></svg>Balances</li>
      <li><svg class="ico"><use href="#i-tx"/></svg>Transactions</li>
      <li><svg class="ico"><use href="#i-send"/></svg>Send Money</li>
      <li><svg class="ico"><use href="#i-acct"/></svg>Create Account</li>
      <li><svg class="ico"><use href="#i-wallet"/></svg>My Wallet Address</li>
      <li><svg class="ico"><use href="#i-msg"/></svg>Private Message</li>
      <li><svg class="ico"><use href="#i-buy"/></svg>Buy Cryptocurrency</li>
      <li><svg class="ico"><use href="#i-nft"/></svg>NFTS</li>
      <li><svg class="ico"><use href="#i-earn"/></svg>Earn</li>
      <li><svg class="ico"><use href="#i-files"/></svg>Files/Vault</li>
      <li><svg class="ico"><use href="#i-wealth"/></svg>Wealth</li>
      <li><svg class="ico"><use href="#i-edu"/></svg>Education</li>
      <li class="active"><svg class="ico"><use href="#i-news"/></svg>News<svg class="tab"><use href="#i-tab"/></svg></li>
      <li><svg class="ico"><use href="#i-faq"/></svg>FAQS</li>
      <li><svg class="ico"><use href="#i-contact"/></svg>Contact Us</li>
    </ul></aside>
  <header class="topbar"><div class="search">Search<span class="search-btn"><svg width="3" height="3"><use href="#i-search"/></svg></span></div>
    <div class="price">ZORBS<svg><use href="#i-up"/></svg><br>$ 1.75</div>
    <div class="auth"><svg><use href="#i-user"/></svg>LOGIN / <svg><use href="#i-signin"/></svg>SIGN UP</div></header>
  <div class="card"><h2 class="card-title">NEWS</h2>
    <p class="copy">Lorem ipsum dolor sit amet, consectetur adipiscing elit, sed do eiusmod tempor incididunt ut labore et dolore magna aliqua. Ut enim ad minim veniam, quis nostrud exercitation ullamco laboris nisi ut aliquip ex ea commodo consequat. Duis aute irure dolor in reprehenderit in voluptate velit esse cillum dolore eu fugiat nulla pariatur. Excepteur sint occaecat cupidatat non proident, sunt in culpa qui officia deserunt mollit anim id est laborum.</p></div>
</section>

<!-- FAQs -->
<section class="screen">
  <aside class="sidebar"><div class="brand">PorlenPurse Apps</div>
    <ul class="nav">
      <li><svg class="ico"><use href="#i-bal"/></svg>Balances</li>
      <li><svg class="ico"><use href="#i-tx"/></svg>Transactions</li>
      <li><svg class="ico"><use href="#i-send"/></svg>Send Money</li>
      <li><svg class="ico"><use href="#i-acct"/></svg>Create Account</li>
      <li><svg class="ico"><use href="#i-wallet"/></svg>My Wallet Address</li>
      <li><svg class="ico"><use href="#i-msg"/></svg>Private Message</li>
      <li><svg class="ico"><use href="#i-buy"/></svg>Buy Cryptocurrency</li>
      <li><svg class="ico"><use href="#i-nft"/></svg>NFTS</li>
      <li><svg class="ico"><use href="#i-earn"/></svg>Earn</li>
      <li><svg class="ico"><use href="#i-files"/></svg>Files/Vault</li>
      <li><svg class="ico"><use href="#i-wealth"/></svg>Wealth</li>
      <li><svg class="ico"><use href="#i-edu"/></svg>Education</li>
      <li><svg class="ico"><use href="#i-news"/></svg>News</li>
      <li class="active"><svg class="ico"><use href="#i-faq"/></svg>FAQS<svg class="tab"><use href="#i-tab"/></svg></li>
      <li><svg class="ico"><use href="#i-contact"/></svg>Contact Us</li>
    </ul></aside>
  <header class="topbar"><div class="search">Search<span class="search-btn"><svg width="3" height="3"><use href="#i-search"/></svg></span></div>
    <div class="price">ZORBS<svg><use href="#i-up"/></svg><br>$ 1.75</div>
    <div class="auth"><svg><use href="#i-user"/></svg>LOGIN / <svg><use href="#i-signin"/></svg>SIGN UP</div></header>
  <div class="card tall faq"><h2 class="card-title">FAQS</h2>
    <h3>What is Vextaro?</h3>
    <ul>
      <li>Vextaro is a blockchain platform joining central and decentralized tools so members can make simple, secure and low cost transfers and trades from one wallet.</li>
      <li>Vextaro rewards users for using platform services by giving ZORBS holders rewards on the network.</li>
      <li>Vextaro runs linked services using bank transfers, debit cards, credit cards and its own private ledger.</li>
    </ul>
    <h3>How is Vextaro organized?</h3>
    <ul>
      <li>Vextaro Inc is a registered company that services accounts for all clients and debit cards for local users.</li>
      <li>Vextaro OU is a partner company that provides debit card services to overseas users.</li>
    </ul>
    <h3>Does Vextaro need licenses to provide services?</h3>
    <ul>
      <li>Vextaro operates under the guidance of regulators and partners with licensed firms to offer services worldwide.</li>
      <li>Vextaro partners with trusted providers to offer compliant services including identity checks, insured accounts, custody and transfers.</li>
      <li>Vextaro is partnered with a card provider to offer compliant debit card services.</li>
    </ul></div>
</section>

<!-- Contact Us -->
<section class="screen">
  <aside class="sidebar"><div class="brand">PorlenPurse Apps</div>
    <ul class="nav">
      <li><svg class="ico"><use href="#i-bal"/></svg>Balances</li>
      <li><svg class="ico"><use href="#i-tx"/></svg>Transactions</li>
      <li><svg class="ico"><use href="#i-send"/></svg>Send Money</li>
      <li><svg class="ico"><use href="#i-acct"/></svg>Create Account</li>
      <li><svg class="ico"><use href="#i-wallet"/></svg>My Wallet Address</li>
      <li><svg class="ico"><use href="#i-msg"/></svg>Private Message</li>
      <li><svg class="ico"><use href="#i-buy"/></svg>Buy Cryptocurrency</li>
      <li><svg class="ico"><use href="#i-nft"/></svg>NFTS</li>
      <li><svg class="ico"><use href="#i-earn"/></svg>Earn</li>
      <li><svg class="ico"><use href="#i-files"/></svg>Files/Vault</li>
      <li><svg class="ico"><use href="#i-wealth"/></svg>Wealth</li>
      <li><svg class="ico"><use href="#i-edu"/></svg>Education</li>
      <li><svg class="ico"><use href="#i-news"/></svg>News</li>
      <li><svg class="ico"><use href="#i-faq"/></svg>FAQS</li>
      <li class="active"><svg class="ico"><use href="#i-contact"/></svg>Contact Us<svg class="tab"><use href="#i-tab"/></svg></li>
    </ul></aside>
  <header class="topbar"><div class="search">Search<span class="search-btn"><svg width="3" height="3"><use href="#i-search"/></svg></span></div>
    <div class="price">ZORBS<svg><use href="#i-up"/></svg><br>$ 1.75</div>
    <div class="auth"><svg><use href="#i-user"/></svg>LOGIN / <svg><use href="#i-signin"/></svg>SIGN UP</div></header>
  <div class="card"><h2 class="card-title">CONTACT US</h2>
    <div class="form"><div class="field">Enter message</div>
      <div class="btn">SEND</div></div></div>
</section>

</main>
</body>
</html>
```